TA BRAMLEY BUSINESS CARD DESIGN PROJECT

We need to utilize our logo that was expertly created on PixelHarbor and now need to match this with a business card design.

```html
<!DOCTYPE html>
<html lang="en">
<head>
<meta charset="utf-8">
<title>TA Bramley Business Card</title>
<link href="https://fonts.googleapis.com/css2?family=Montserrat:wght@400;500;700&display=swap" rel="stylesheet">
<style>
  :root {
    --brand-blue: #1059ac;
    --ink: #151515;
    --paper: #ffffff;
    --backdrop: #d9d9d9;
    --text-light: #f2f2f2;
  }
  * { margin: 0; padding: 0; box-sizing: border-box; }
  html, body { width: 1200px; height: 900px; overflow: hidden; }
  body {
    background: var(--backdrop);
    font-family: "Montserrat", Arial, sans-serif;
    position: relative;
  }
  .card {
    position: absolute;
    width: 640px;
    height: 366px;
    border-radius: 22px;
    overflow: hidden;
    box-shadow: 0 10px 28px rgba(0,0,0,0.25);
  }
  .card-front {
    left: 60px; top: 60px;
    background: var(--brand-blue);
    display: flex; align-items: center; justify-content: center;
  }
  .front-wordmark {
    color: var(--paper);
    font-weight: 700;
    font-size: 64px;
    letter-spacing: 10px;
  }
  .card-back {
    left: 500px; top: 474px;
    background: var(--paper);
  }
  .back-shapes { position: absolute; inset: 0; }
  .back-wordmark {
    position: absolute;
    right: 40px; top: 52px;
    color: var(--brand-blue);
    font-weight: 700;
    font-size: 34px;
    letter-spacing: 5px;
  }
  .contact {
    position: absolute;
    left: 40px; top: 214px;
    color: var(--text-light);
  }
  .contact-name {
    color: var(--brand-blue);
    font-weight: 700;
    font-size: 19px;
    letter-spacing: 0.5px;
  }
  .contact-role { font-size: 13px; margin-bottom: 8px; }
  .contact-list { list-style: none; font-size: 12.5px; line-height: 19px; }
  .contact-list li { display: flex; align-items: center; gap: 8px; }
  .contact-list svg { width: 12px; height: 12px; fill: var(--brand-blue); flex: none; }
  .contact-address { font-size: 12.5px; line-height: 18px; margin-top: 8px; }
</style>
</head>
<body>
  <section class="card card-front">
    <span class="front-wordmark">TA BRAMLEY</span>
  </section>

  <section class="card card-back">
    <svg class="back-shapes" viewBox="0 0 640 366" width="640" height="366">
      <path d="M360,230 C500,268 606,215 626,60 C632,170 560,258 360,232 Z" fill="var(--brand-blue)"/>
      <path d="M0,366 L0,250 C110,170 250,190 380,228 C510,265 608,212 640,90 L640,366 Z" fill="var(--ink)"/>
    </svg>
    <span class="back-wordmark">TA BRAMLEY</span>
    <div class="contact">
      <p class="contact-name">MARTIN HALE</p>
      <p class="contact-role">Managing Director</p>
      <ul class="contact-list">
        <li><svg viewBox="0 0 24 24"><path d="M6.6 10.8a15 15 0 0 0 6.6 6.6l2.2-2.2a1 1 0 0 1 1-.25 11.4 11.4 0 0 0 3.6.57 1 1 0 0 1 1 1V20a1 1 0 0 1-1 1A17 17 0 0 1 3 4a1 1 0 0 1 1-1h3.5a1 1 0 0 1 1 1c0 1.25.2 2.45.57 3.57a1 1 0 0 1-.25 1z"/></svg>123 456 789</li>
        <li><svg viewBox="0 0 24 24"><rect x="4" y="3" width="16" height="18" rx="2"/></svg>123 456 789</li>
        <li><svg viewBox="0 0 24 24"><path d="M2 5h20v14H2z M2 5l10 8 10-8" /></svg>info@tabramley.com</li>
        <li><svg viewBox="0 0 24 24"><circle cx="12" cy="12" r="10"/></svg>www.tabramley.com</li>
      </ul>
      <p class="contact-address">Your address, City<br>State, Zip 1234</p>
    </div>
  </section>
</body>
</html>
```